Forensic Document Examiner, looking for contemporary update to my stationery design.

Looking for professional, classy logo design for stationery and business cards. My current stationery and business card is attached.I believe a logo image makes a header section interesting, so an intriguing design of a pen, feathered pen, microscope, magnifying glass, etc., would be appropriate. I have been in the business for over 30 years. I leave ideas to the imagination of the designer.My work involves mainly, the comparison of signatures and handwriting. I also resolve alterations, obliterations, and work as shown on my website: www.documentexaminer.infoThe image produced will be printed on quality white stationery and envelopes. The stationery will be photocopied by my clients, so the images should be reproducible. The business cards may be designed in other than white.

Target Market(s)

Attorneys

Font styles to use
Sans Serif

Colors

Designer to choose colors to be used in the design.

Requirements
Must have
• Image suitable for white stationery and photocopying.
• Classy logo and image; no casual fonts.
Nice to have
• Intriguing, contemporary design incorporating a relevant logo to my work.

```html
<!DOCTYPE html>
<html lang="en">
<head>
<meta charset="utf-8">
<title>Daniel R. Whitfield – Stationery</title>
<link rel="stylesheet" href="https://fonts.googleapis.com/css2?family=Didact+Gothic&display=swap">
<style>
  :root {
    --backdrop: #dcdcdc;
    --paper: #f7f7f7;
    --ink: #4a4a4a;
    --brand-blue: #2e2f9c;
    --brand-gold: #d6a91a;
    --mark-grey: #b7b9c8;
    --flap-line: #e2e2e2;
    --signature: #2c2f38;
  }
  * { box-sizing: border-box; margin: 0; padding: 0; }
  html, body { width: 1200px; height: 877px; overflow: hidden; }
  body {
    background: var(--backdrop);
    font-family: "Didact Gothic", sans-serif;
    color: var(--ink);
    position: relative;
  }
  .sheet { position: absolute; background: var(--paper); }

  /* Letterhead */
  .letterhead { left: 59px; top: 66px; width: 527px; height: 742px; }
  .contact-list { position: absolute; left: 45px; top: 46px; list-style: none; font-size: 8px; line-height: 10.6px; color: var(--ink); }
  .contact-list li { display: flex; align-items: center; gap: 5px; }
  .contact-list svg { width: 7px; height: 7px; fill: var(--brand-blue); flex: none; }
  .brand { position: absolute; display: flex; align-items: center; gap: 6px; }
  .brand-dot { width: 14px; height: 14px; border-radius: 50%; background: var(--mark-grey); flex: none; }
  .brand-text { display: flex; flex-direction: column; }
  .brand-name { color: var(--brand-blue); font-size: 16px; line-height: 17px; letter-spacing: 1px; text-transform: uppercase; }
  .brand-tagline { color: var(--brand-gold); font-size: 7px; line-height: 9px; }
  .letterhead .brand { right: 42px; top: 48px; }
  .salutation { position: absolute; left: 45px; top: 215px; font-size: 13.5px; color: #555; }
  .letter-body { position: absolute; left: 45px; top: 252px; width: 438px; font-size: 7.4px; line-height: 11.4px; text-align: justify; }
  .letter-body p + p { margin-top: 11.4px; }
  .closing { position: absolute; left: 45px; top: 490px; font-size: 7.6px; }
  .signature { position: absolute; left: 45px; top: 506px; width: 61px; height: 24px; }

  /* Envelopes */
  .envelope-back { left: 620px; top: 293px; width: 530px; height: 239px; }
  .envelope-back .flap { position: absolute; left: 0; top: 0; width: 530px; height: 80px; }
  .envelope-back .seal-dot { position: absolute; left: 255px; top: 24px; width: 20px; height: 20px; border-radius: 50%; background: var(--mark-grey); }
  .envelope-front { left: 620px; top: 566px; width: 532px; height: 242px; }
  .envelope-front .brand { left: 32px; top: 26px; }
  .return-address { position: absolute; left: 39px; top: 73px; font-size: 8px; color: var(--ink); }
</style>
</head>
<body>

<section class="sheet letterhead">
  <ul class="contact-list">
    <li><svg viewBox="0 0 10 10"><path d="M2 0.5 L3.6 2.6 L2.7 3.6 Q4 6.2 6.4 7.3 L7.4 6.4 L9.5 8 L8.2 9.5 Q3 9 0.5 2 Z"/></svg>(888) 555-0147</li>
    <li><svg viewBox="0 0 10 10"><path d="M0.5 2 H9.5 V8.5 H0.5 Z M0.5 2 L5 5.6 L9.5 2"/></svg>dwhitfield@quillmarkreview.info</li>
    <li><svg viewBox="0 0 10 10"><circle cx="5" cy="5" r="4.5"/></svg>www.quillmarkreview.info</li>
    <li><svg viewBox="0 0 10 10"><path d="M5 0.3 A3.6 3.6 0 0 1 8.6 3.9 C8.6 6.3 5 9.7 5 9.7 C5 9.7 1.4 6.3 1.4 3.9 A3.6 3.6 0 0 1 5 0.3 Z"/></svg>P.O.Box 2184, Salem, OR 97301</li>
  </ul>

  <div class="brand">
    <span class="brand-dot"></span>
    <div class="brand-text">
      <span class="brand-name">Daniel R. Whitfield</span>
      <span class="brand-tagline">Forensic Document Examiner</span>
    </div>
  </div>

  <p class="salutation">Dear Mr. Harlow,</p>

  <div class="letter-body">
    <p>Lorem ipsum dolor sit amet, consectetur adipiscing elit. Donec orci purus, luctus vitae dignissim eu, iaculis sed purus. Vivamus faucibus, ipsum nec aliquet viverra, leo mauris condimentum ligula, sit amet sagittis enim ligula quis arcu. Nam egestas tortor id nisi porttitor mattis. In tortor ante, ultricies in suscipit a, tempus non massa. Vivamus et auctor mi. Fusce vel massa nulla. Phasellus nec eros mauris, et scelerisque orci.</p>
    <p>Donec malesuada orci vitae nulla accumsan porta a id massa. Quisque accumsan iaculis magna sit amet fringilla. Maecenas consequat, magna eget tincidunt semper, odio nibh rutrum mi, id feugiat ante nisi eu risus. Vestibulum nunc orci, rhoncus a placerat in, ultricies in mi. Cras mattis varius eros, vel fringilla nisi suscipit eget. Quisque scelerisque sagittis nulla at porttitor.</p>
    <p>Sed id augue vitae urna euismod commodo aliquet a quam. Pellentesque arcu velit, cursus et malesuada ut, consequat et diam. Nullam erat sem, rhoncus id ullamcorper vitae, rhoncus et arcu. In ultricies ultricies nulla, ut rutrum nisi iaculis at. Donec eu magna a metus ornare faucibus. Fusce aliquet faucibus ultricies. Morbi semper, est id tincidunt gravida, sem arcu adipiscing lacus, ac bibendum nulla leo eu purus. Quisque nec diam sed risus consectetur a ccumsan quis quis nibh. Vestibulum id purus lorem.</p>
    <p>It is a long established fact that a reader will be distracted by the readable content of a page when looking at its layout. The point of using Lorem Ipsum is that it has a more-or-less normal distribution of letters, as opposed to using 'Content here, content here', making it look like readable English. Many desktop publishing packages</p>
  </div>

  <p class="closing">Sincerely,</p>
  <svg class="signature" role="img" aria-label="Handwritten signature" viewBox="0 0 61 24">
    <rect x="0" y="8" width="61" height="8" rx="4" fill="var(--signature)" opacity="0.25"/>
  </svg>
</section>

<section class="sheet envelope-back">
  <svg class="flap" viewBox="0 0 530 80" aria-hidden="true">
    <path d="M12 0 V58 Q12 71 28 71 H502 Q518 71 518 58 V0" fill="none" stroke="var(--flap-line)" stroke-width="1.5"/>
  </svg>
  <span class="seal-dot"></span>
</section>

<section class="sheet envelope-front">
  <div class="brand">
    <span class="brand-dot"></span>
    <div class="brand-text">
      <span class="brand-name">Daniel R. Whitfield</span>
      <span class="brand-tagline">Forensic Document Examiner</span>
    </div>
  </div>
  <p class="return-address">P.O.Box 2184, Salem, OR 97301</p>
</section>

</body>
</html>
```